Hörbuchcover
Zielgruppe
Spiritueller Hörbuchverlag für ganzheitliche Gesundheit, Glück und Wohlstand.
Aufgabenstellung
Benötigt wird ein schönes quadratisches Cover, 2400x2400 mindestens 72dpi für ein Hörbuchcover.
Auf dem Cover soll eine gelb/orange Rose zu in Form einer Blüte zu sehen sein.
Titel: Goldener Pfad
Untertitel: Emotionen sind der Schlüssel für Gesundheit, Energie & Lebensfreude
Autorenname: Dr. med. Katrin Wollberg
Das Velmira Logo soll unten mittig sitzen.
Es folgen weiterer Hörbücher von dieser Autorin und es wäre gut wenn man die folgenden Cover in einem ähnlichen Stil halten könnte. Ein harmonisches und gut zu erkennendes Design mit hohem Wiedererkennungseffekt. Ich freue mich auf kreative Designvorschläge.
Auf velmira.de kann man sehen wo das Logo sitzen soll.
Herzliche Grüße - Jonas

```html
<!DOCTYPE html>
<html lang="de">
<head>
<meta charset="utf-8">
<title>Goldener Pfad – Hörbuchcover</title>
<link href="https://fonts.googleapis.com/css2?family=Cinzel:wght@500&family=Great+Vibes&family=Montserrat:wght@500;600&family=Marcellus&display=swap" rel="stylesheet">
<style>
  :root {
    --paper: #ece0cf;
    --paper-light: #f1e7d8;
    --ink: #0f2014;
    --band: rgba(243, 234, 220, 0.62);
    --band-strong: rgba(238, 227, 210, 0.92);
    --rose-core: #f8e6c4;
    --rose-mid: #f3c978;
    --rose-edge: #e8874a;
  }
  * { margin: 0; padding: 0; box-sizing: border-box; }
  html, body { width: 1200px; height: 1200px; overflow: hidden; background: var(--paper); }
  .cover {
    position: relative;
    width: 1200px; height: 1200px;
    background: radial-gradient(ellipse at 50% 50%, var(--paper-light) 0%, var(--paper) 75%);
    overflow: hidden;
    color: var(--ink);
  }
  .rose-art {
    position: absolute;
    left: 112px; top: 140px;
    width: 1000px; height: 1040px;
    border-radius: 48% 48% 44% 44%;
    background: radial-gradient(ellipse at 50% 42%, var(--rose-core) 0%, #f6dca4 35%, var(--rose-mid) 60%, var(--rose-edge) 88%, rgba(232,135,74,0) 100%);
  }
  .author {
    position: absolute;
    top: 58px; left: 0; width: 100%;
    text-align: center;
    font-family: "Montserrat", sans-serif;
    font-weight: 500;
    font-size: 38px;
    letter-spacing: 1px;
  }
  .title-band {
    position: absolute;
    left: 0; top: 320px;
    width: 100%; height: 472px;
    background: var(--band);
  }
  .title-main {
    position: absolute;
    top: 372px; left: 0; width: 100%;
    text-align: center;
    font-family: "Cinzel", serif;
    font-weight: 500;
    font-size: 146px;
    letter-spacing: 2px;
    line-height: 1;
  }
  .title-script {
    position: absolute;
    top: 500px; left: 20px; width: 100%;
    text-align: center;
    font-family: "Great Vibes", cursive;
    font-size: 240px;
    line-height: 1;
  }
  .subtitle-band {
    position: absolute;
    left: 0; top: 863px;
    width: 100%; height: 122px;
    background: var(--band-strong);
  }
  .subtitle {
    position: absolute;
    top: 882px; left: 0; width: 100%;
    text-align: center;
    font-family: "Marcellus", serif;
    font-size: 27px;
    letter-spacing: 1.5px;
    line-height: 1.5;
    padding-right: 30px;
  }
  .publisher {
    position: absolute;
    bottom: 26px; left: 0; width: 100%;
    display: flex; justify-content: center; align-items: center; gap: 14px;
    font-family: "Montserrat", sans-serif;
    font-weight: 600;
    font-size: 38px;
    letter-spacing: 6px;
  }
  .publisher-dot {
    width: 26px; height: 26px;
    border: 3px solid var(--ink);
    border-radius: 50%;
  }
</style>
</head>
<body>
  <div class="cover">
    <div class="rose-art" role="img" aria-label="Aquarell einer gelb-orangen Rosenblüte mit grünen Blättern"></div>
    <div class="author">DR. MED. KATRIN WOLLBERG</div>
    <div class="title-band"></div>
    <h1 class="title-main">GOLDENER</h1>
    <div class="title-script">Pfad</div>
    <div class="subtitle-band"></div>
    <p class="subtitle">EMOTIONEN SIND DER SCHLÜSSEL FÜR GESUNDHEIT,<br>ENERGIE &amp; LEBENSFREUDE</p>
    <div class="publisher"><span class="publisher-dot"></span><span>VELMIRA</span></div>
  </div>
</body>
</html>
```